website design for M&T Electric

A portfolio website for a high end commercial and residential electrical contracting company. The current site mandtelectric.example does not represent the current direction but the images in the gallery give you an idea of the work we do. Current logo will be uploaded shortly but is black text on white background.
Target Market(s)
General Contractors, Residential Home Owners, clients intersted in Velmora home automation.
Industry/Entity Type
Electrician
Coding
Coded - Design and coding required
Number of Pages Required
2 page
Font styles to use
Sans Serif
Colors
Designer to choose colors to be used in the design.
Requirements
Must have
- Portfolio section highlighting different service areas and products (Velmora Housepilot, etc)

```html
<!DOCTYPE html>
<html lang="en">
<head>
<meta charset="utf-8">
<title>M&amp;T Electric</title>
<link rel="stylesheet" href="https://fonts.googleapis.com/css2?family=Raleway:wght@400;600;700;800&family=Open+Sans:wght@400;600;700&display=swap">
<style>
:root{
  --orange:#e8581b;
  --orange-dark:#c94a12;
  --ink:#1e1e1e;
  --text:#444;
  --muted:#777;
  --gray-band:#e4e4e4;
  --white:#fff;
  --night:#141414;
  --line:#cfcfcf;
}
*{box-sizing:border-box;margin:0;padding:0}
html,body{width:1200px;height:3030px;overflow:hidden;background:var(--white);font-family:"Open Sans",Arial,sans-serif;color:var(--text)}
.page{position:relative;width:1200px;height:3030px}
.abs{position:absolute}
/* header + hero */
.hero{position:absolute;left:0;top:0;width:1200px;height:495px;background:linear-gradient(160deg,#1b1a3a 0%,#3b2a52 30%,#2f5d3b 55%,#a8442e 80%,#3b1e14 100%)}
.hero-shade{position:absolute;inset:0;background:linear-gradient(90deg,rgba(10,10,25,.65) 0%,rgba(10,10,25,.15) 60%,rgba(0,0,0,0) 100%)}
.topbar{position:absolute;left:0;top:0;width:1200px;height:66px;background:rgba(15,15,30,.85)}
.logo{position:absolute;left:98px;top:12px;font-family:"Raleway",sans-serif;font-weight:400;font-size:34px;color:var(--white);letter-spacing:.5px}
.nav{position:absolute;right:100px;top:20px;display:flex;gap:32px;font-family:"Open Sans",sans-serif;font-size:16px;color:var(--white)}
.hero-title{position:absolute;left:98px;top:162px;font-family:"Raleway",sans-serif;font-weight:700;font-size:44px;line-height:50px;color:var(--white)}
.hero-sub{position:absolute;left:98px;top:266px;font-family:"Raleway",sans-serif;font-size:26px;color:var(--white)}
.btn-outline{position:absolute;display:flex;align-items:center;justify-content:center;gap:8px;border:2px solid var(--white);border-radius:6px;font-family:"Open Sans",sans-serif;font-weight:600;color:var(--white);text-transform:uppercase}
.hero-btn{left:98px;top:345px;width:161px;height:50px;font-size:16px}
.bulbs{position:absolute;left:40px;top:178px}
/* section titles */
.sec-title{position:absolute;left:0;width:1200px;text-align:center;font-family:"Raleway",sans-serif;font-weight:700;font-size:27px;color:var(--ink);text-transform:uppercase}
.divider{position:absolute;left:526px;width:148px;height:18px}
/* services */
.svc{position:absolute;top:648px;width:240px;height:210px;border:3px solid #ececec;overflow:hidden}
.svc .ph{position:absolute;inset:0}
.svc .tag{position:absolute;left:0;top:0;height:34px;padding:0 34px 0 8px;background:var(--orange);clip-path:polygon(0 0,100% 0,82% 100%,0 100%);font-family:"Raleway",sans-serif;font-weight:700;font-size:15px;line-height:34px;color:var(--white);text-transform:uppercase}
/* about */
.about-band{position:absolute;left:0;top:925px;width:1200px;height:433px;background:var(--gray-band)}
.about-text{position:absolute;left:100px;top:1064px;width:530px;font-size:12.5px;line-height:23px;color:#333}
.about-text p{margin-bottom:16px}
.btn-orange{position:absolute;display:flex;align-items:center;justify-content:center;gap:6px;border:2px solid var(--orange);border-radius:6px;color:var(--orange);font-weight:600;text-transform:uppercase}
.about-img{position:absolute;left:660px;top:1052px;width:440px;height:254px;border:3px solid #f2f2f2;background:linear-gradient(180deg,#b9bec6 0%,#a7a8a4 45%,#6f6a5e 70%,#5a5a5a 100%)}
/* gallery */
.tabs{position:absolute;left:0;top:1495px;width:1200px;display:flex;justify-content:center;gap:38px;font-family:"Raleway",sans-serif;font-weight:600;font-size:15px;color:#333}
.tabs span{padding-bottom:6px;border-bottom:2px solid #ccc;text-transform:uppercase}
.tabs .active{border-bottom-color:var(--orange)}
.gal{position:absolute;top:1550px;width:328px;height:207px;border:3px solid #ececec}
/* cta */
.cta{position:absolute;left:0;top:1826px;width:1200px;height:242px;background:var(--orange)}
.cta h2{position:absolute;left:0;top:50px;width:1200px;text-align:center;font-family:"Open Sans",sans-serif;font-weight:600;font-size:27px;color:var(--white)}
.cta p{position:absolute;left:0;top:92px;width:1200px;text-align:center;font-size:16px;font-weight:600;color:#fde7d9}
.cta .btn-outline{top:132px;height:50px;font-size:17px;text-transform:none}
/* testimonial */
.avatar{position:absolute;left:545px;top:2197px;width:110px;height:110px;border-radius:50%;border:4px solid #ddd;background:radial-gradient(circle at 50% 40%,#b89a84 0%,#6f5a4e 55%,#2b2b33 100%)}
.quote{position:absolute;left:230px;top:2313px;width:740px;text-align:center;font-size:13.5px;line-height:24px;color:#555}
.person{position:absolute;left:0;top:2374px;width:1200px;text-align:center;font-family:"Raleway",sans-serif;font-weight:700;font-size:16px;color:var(--ink);text-transform:uppercase}
.role{position:absolute;left:0;top:2402px;width:1200px;text-align:center;font-size:13px;color:#333}
/* contact */
.contact{position:absolute;left:0;top:2525px;width:1200px;height:505px;background:linear-gradient(180deg,#1c1c1c 0%,#2a2622 45%,#171717 100%)}
.contact-shade{position:absolute;inset:0;background:rgba(0,0,0,.45)}
.contact .sec-title{color:var(--white);top:60px}
.contact .lede{position:absolute;left:0;top:100px;width:1200px;text-align:center;font-size:16px;color:#ddd}
.field{position:absolute;border-bottom:1px solid #bbb;font-size:13px;color:var(--white);padding-bottom:6px}
.send{position:absolute;left:548px;top:311px;width:102px;height:31px;border:1px solid #ddd;border-radius:7px;display:flex;align-items:center;justify-content:center;font-size:14px;color:var(--white)}
.info{position:absolute;top:395px;display:flex;align-items:center;gap:14px;font-size:12px;line-height:21px;color:var(--white)}
.icon-c{width:34px;height:34px;border-radius:50%;border:2px solid var(--orange);display:flex;align-items:center;justify-content:center;flex:none}
.copy{position:absolute;left:98px;top:470px;font-size:12px;color:#ddd}
.social{position:absolute;left:940px;top:472px;display:flex;gap:24px}
.social span{width:12px;height:12px;border-radius:50%;background:var(--orange)}
</style>
</head>
<body>
<div class="page">

  <!-- hero -->
  <header class="hero" role="img" aria-label="Night photo of a lit glass-and-steel canopy over a city street">
    <div class="hero-shade"></div>
  </header>
  <div class="topbar"></div>
  <div class="logo">M&amp;T Electric</div>
  <nav class="nav"><span>Home</span><span>Gallery</span><span>Specialty Services</span><span>About</span><span>Contact</span></nav>

  <svg class="bulbs" width="16" height="110" viewBox="0 0 16 110" aria-hidden="true">
    <g fill="none" stroke="#fff" stroke-width="1.6">
      <path d="M8 2a5 5 0 0 1 3 9v3H5v-3A5 5 0 0 1 8 2z"/>
      <path d="M8 25a5 5 0 0 1 3 9v3H5v-3a5 5 0 0 1 3-9z"/>
      <path d="M8 48a5 5 0 0 1 3 9v3H5v-3a5 5 0 0 1 3-9z" stroke="#e8581b"/>
      <path d="M8 71a5 5 0 0 1 3 9v3H5v-3a5 5 0 0 1 3-9z"/>
      <path d="M8 94a5 5 0 0 1 3 9v3H5v-3a5 5 0 0 1 3-9z"/>
    </g>
  </svg>

  <h1 class="hero-title">We're the Current<br>Specialist!</h1>
  <div class="hero-sub">Keeping you wired</div>
  <div class="btn-outline hero-btn">
    <svg width="12" height="20" viewBox="0 0 12 20"><path d="M8 0L1 11h4l-2 9 8-12H7z" fill="#e8581b"/></svg>Learn More
  </div>

  <!-- services -->
  <h2 class="sec-title" style="top:554px">Our Services</h2>
  <svg class="divider" style="top:588px" viewBox="0 0 148 18" aria-hidden="true">
    <line x1="0" y1="14" x2="60" y2="14" stroke="#e8581b" stroke-width="1.5" stroke-dasharray="2 3"/>
    <line x1="88" y1="14" x2="148" y2="14" stroke="#e8581b" stroke-width="1.5" stroke-dasharray="2 3"/>
    <path d="M74 1a5 5 0 0 1 3 9v3h-6v-3a5 5 0 0 1 3-9z" fill="none" stroke="#e8581b" stroke-width="1.6"/>
  </svg>

  <div class="svc" style="left:98px"><div class="ph" role="img" aria-label="Bright open-plan living room with dimmable lighting" style="background:linear-gradient(180deg,#e4e0d8,#a89b88 60%,#5b4635)"></div><div class="tag">Velmora Dimming</div></div>
  <div class="svc" style="left:352px"><div class="ph" role="img" aria-label="Dark modern kitchen with blue accent lighting and motorized shades" style="background:linear-gradient(180deg,#2c2f3c,#3c4b7a 55%,#1a1a22)"></div><div class="tag">Velmora Shades</div></div>
  <div class="svc" style="left:606px"><div class="ph" role="img" aria-label="Large standby generator on a trailer" style="background:linear-gradient(180deg,#cfd2d6,#b9bbbc 55%,#6d6d6b)"></div><div class="tag">Generator</div></div>
  <div class="svc" style="left:860px"><div class="ph" role="img" aria-label="Group of white LED light bulbs on a warm background" style="background:linear-gradient(135deg,#f1ece6,#d8c5b6 50%,#a8704f)"></div><div class="tag">LED Lighting</div></div>

  <!-- about -->
  <section class="about-band"></section>
  <h2 class="sec-title" style="top:971px">About Us</h2>
  <svg class="divider" style="top:1003px" viewBox="0 0 148 18" aria-hidden="true">
    <line x1="0" y1="14" x2="60" y2="14" stroke="#e8581b" stroke-width="1.5" stroke-dasharray="2 3"/>
    <line x1="88" y1="14" x2="148" y2="14" stroke="#e8581b" stroke-width="1.5" stroke-dasharray="2 3"/>
    <path d="M74 1a5 5 0 0 1 3 9v3h-6v-3a5 5 0 0 1 3-9z" fill="none" stroke="#e8581b" stroke-width="1.6"/>
  </svg>
  <div class="about-text">
    <p>We are locally owned and operated which makes our services causal as they are done by friendly and helpful technicians.</p>
    <p>M &amp; T Electric is a full service electrical contracting shop. We offer commercial, residential, light industrial, and agricultural services. We're Velmora Housepilot and Velmora Motorized Shades certified, as well as an authorized Corvane generator dealer. We've served the Wood River and South Central Idaho area for over 18 years.</p>
  </div>
  <div class="btn-orange" style="left:100px;top:1245px;width:143px;height:44px;font-size:14px">
    <svg width="10" height="18" viewBox="0 0 12 20"><path d="M8 0L1 11h4l-2 9 8-12H7z" fill="#e8581b"/></svg>Learn More
  </div>
  <div class="about-img" role="img" aria-label="Single-storey company office building with a gabled roof"></div>

  <!-- gallery -->
  <h2 class="sec-title" style="top:1420px">Our Gallery</h2>
  <svg class="divider" style="top:1452px" viewBox="0 0 148 18" aria-hidden="true">
    <line x1="0" y1="14" x2="60" y2="14" stroke="#e8581b" stroke-width="1.5" stroke-dasharray="2 3"/>
    <line x1="88" y1="14" x2="148" y2="14" stroke="#e8581b" stroke-width="1.5" stroke-dasharray="2 3"/>
    <path d="M74 1a5 5 0 0 1 3 9v3h-6v-3a5 5 0 0 1 3-9z" fill="none" stroke="#e8581b" stroke-width="1.6"/>
  </svg>
  <div class="tabs"><span class="active">Commercial</span><span>Residential</span><span>Landscape</span></div>
  <div class="gal" style="left:100px" role="img" aria-label="Stone and timber lodge-style commercial building" style="" ><div style="position:absolute;inset:0;background:linear-gradient(180deg,#6a5a55,#7b655a 50%,#3e3a36)"></div></div>
  <div class="gal" style="left:436px" role="img" aria-label="Modern three-storey office building under blue sky"><div style="position:absolute;inset:0;background:linear-gradient(180deg,#3d6fb4,#8a929a 45%,#5e6064)"></div></div>
  <div class="gal" style="left:772px" role="img" aria-label="Mixed-use stone building on a street corner"><div style="position:absolute;inset:0;background:linear-gradient(180deg,#8fb0d4,#8a7464 50%,#4a4a44)"></div></div>

  <!-- call to action -->
  <section class="cta">
    <h2>Do you need help with electrical maintenance?</h2>
    <p>Contact us - our technicians are ready to help you solve that issue.</p>
    <div class="btn-outline" style="left:384px;width:159px">
      <svg width="16" height="16" viewBox="0 0 24 24"><path d="M6.6 10.8a15 15 0 0 0 6.6 6.6l2.2-2.2a1 1 0 0 1 1-.25 11.4 11.4 0 0 0 3.6.6 1 1 0 0 1 1 1V20a1 1 0 0 1-1 1A17 17 0 0 1 3 4a1 1 0 0 1 1-1h3.5a1 1 0 0 1 1 1c0 1.25.2 2.45.6 3.6a1 1 0 0 1-.25 1z" fill="#fff"/></svg>Call Us Now
    </div>
    <div class="btn-outline" style="left:564px;width:253px">
      <svg width="12" height="20" viewBox="0 0 12 20"><path d="M8 0L1 11h4l-2 9 8-12H7z" fill="#fff"/></svg>Request A Free Estimate
    </div>
  </section>

  <!-- testimonial -->
  <h2 class="sec-title" style="top:2128px">Our Testimonial</h2>
  <svg class="divider" style="top:2160px;left:496px;width:208px" viewBox="0 0 208 18" aria-hidden="true">
    <line x1="0" y1="14" x2="90" y2="14" stroke="#e8581b" stroke-width="1.5" stroke-dasharray="2 3"/>
    <line x1="118" y1="14" x2="208" y2="14" stroke="#e8581b" stroke-width="1.5" stroke-dasharray="2 3"/>
    <path d="M104 1a5 5 0 0 1 3 9v3h-6v-3a5 5 0 0 1 3-9z" fill="none" stroke="#e8581b" stroke-width="1.6"/>
  </svg>
  <div class="avatar" role="img" aria-label="Client portrait photo"></div>
  <p class="quote">"Lorem ipsum dolor sit amet, consectetur adipiscing elit, sed do eiusmod tempor incididunt ut labore et dolore magna aliqua. Ut enim ad minim veniam, quis nostrud exercitation ullamco laboris"</p>
  <div class="person">Marc Delane</div>
  <div class="role">Manager</div>
  <svg class="abs" style="left:562px;top:2438px" width="76" height="18" viewBox="0 0 76 18" aria-hidden="true">
    <g fill="none" stroke="#333" stroke-width="1.4">
      <path d="M6 2a4 4 0 0 1 2.5 7.2V12h-5V9.2A4 4 0 0 1 6 2z"/>
      <path d="M22 2a4 4 0 0 1 2.5 7.2V12h-5V9.2A4 4 0 0 1 22 2z"/>
      <path d="M38 2a4 4 0 0 1 2.5 7.2V12h-5V9.2A4 4 0 0 1 38 2z" stroke="#e8581b"/>
      <path d="M54 2a4 4 0 0 1 2.5 7.2V12h-5V9.2A4 4 0 0 1 54 2z"/>
      <path d="M70 2a4 4 0 0 1 2.5 7.2V12h-5V9.2A4 4 0 0 1 70 2z"/>
    </g>
  </svg>

  <!-- contact -->
  <section class="contact" role="img" aria-label="Dim evening photo of a large timber house">
    <div class="contact-shade"></div>
    <h2 class="sec-title">Contact Us</h2>
    <p class="lede">Get in touch with us (or) Contact us still any queries.</p>
    <svg class="divider" style="top:135px;left:496px;width:208px" viewBox="0 0 208 18" aria-hidden="true">
      <line x1="0" y1="14" x2="90" y2="14" stroke="#e8581b" stroke-width="1.5" stroke-dasharray="2 3"/>
      <line x1="118" y1="14" x2="208" y2="14" stroke="#e8581b" stroke-width="1.5" stroke-dasharray="2 3"/>
      <path d="M104 1a5 5 0 0 1 3 9v3h-6v-3a5 5 0 0 1 3-9z" fill="none" stroke="#e8581b" stroke-width="1.6"/>
    </svg>
    <div class="field" style="left:98px;top:172px;width:357px">Full Name</div>
    <div class="field" style="left:742px;top:172px;width:358px">Email Address</div>
    <div class="field" style="left:422px;top:230px;width:356px;height:38px">Message</div>
    <div class="send">SEND NOW</div>

    <div class="info" style="left:98px">
      <div class="icon-c"><svg width="14" height="12" viewBox="0 0 14 12"><rect x="0.5" y="1" width="13" height="10" rx="1" fill="#e8581b"/><path d="M1 2l6 5 6-5" stroke="#fff" stroke-width="1.2" fill="none"/></svg></div>
      <div>dwarren@mandtelectric.example<br>cpeters@mandtelectric.example</div>
    </div>
    <div class="info" style="left:537px">
      <div class="icon-c"><svg width="12" height="16" viewBox="0 0 12 16"><path d="M6 0a6 6 0 0 1 6 6c0 4-6 10-6 10S0 10 0 6a6 6 0 0 1 6-6z" fill="#e8581b"/><circle cx="6" cy="6" r="2" fill="#fff"/></svg></div>
      <div>2250 Ridgeline Road, PO Box 4410,<br>Alder, ID 83000</div>
    </div>
    <div class="info" style="left:976px">
      <div class="icon-c"><svg width="14" height="14" viewBox="0 0 24 24"><path d="M6.6 10.8a15 15 0 0 0 6.6 6.6l2.2-2.2a1 1 0 0 1 1-.25 11.4 11.4 0 0 0 3.6.6 1 1 0 0 1 1 1V20a1 1 0 0 1-1 1A17 17 0 0 1 3 4a1 1 0 0 1 1-1h3.5a1 1 0 0 1 1 1c0 1.25.2 2.45.6 3.6a1 1 0 0 1-.25 1z" fill="#e8581b"/></svg></div>
      <div>(208) 555-0147</div>
    </div>

    <div class="copy">© Copyright 2017 Mandtelectric. All Rights Reserved</div>
    <div class="social" aria-label="Social links"><span></span><span></span><span></span><span></span><span></span></div>
  </section>

</div>
</body>
</html>
```